Business Card - high end, modern health care

Hey designers!

We need a double sided business card for the boutique, cutting edge physical therapy rehabilitation centre in Sydney's Northern Beaches.

With the most qualified physios in the area The Harbourview Motion Clinic does what other physiotherapy practices do not, we take our time with our patients giving them longer appointments, better physios and therefor faster results!

We guarantee that the service people receive at THMC will be unparalleled.

Hence we need a business card to reflect our modern, boutique, high end service. The final design needs to reflect that we are in a class of our own yet with the feel of beachside retreat.

Below I have attached our logo in both blue on white and white on blue. The exact colour is;
and the font that we have used in our logo is Tex Gyre Aventador.

I like the idea of the blue as the main colour as it is more eye catching and our signage onto the main road will be in this blue and in the interest of consistency across marketing the blue needs to be a part of the design. However I would appreciate a few designs onto a wooden background as this is a visual theme within the fitout of the practice.

The design needs to be of standard size (91x55mm).

Target Market(s)

We target people who have an end outcome in mind and those who have had poor experiences with other providers and ensure that everyone gets the care that they deserve with a premium service that is tailored to the individuals circumstances. As a premium service, the target market is highly educated, business and tech savvy with the additional target market of elderly people who have self funded their retirement and see value in paying for the best ongoing rehabilitation to maintain independence.

Industry/Entity Type

Physical Therapy

Contact Information for Business Card

Name, designation( Titled Musculoskeletal Physiotherapist... there will also be those in the company that have multiple designations ie 5 or 6 words long), phone number, email, facebook, instagram, address

Font styles to use
Sans Serif

Colors

Designer to choose colors to be used in the design.

Requirements
Must have
• Front - The logo as large as possible, blue or wooden theme, and all of the important details.
• Back - A blank space/lines on which to write appointment times (no "Appointment, date, time" etc.)
Nice to have
• facebook url
• logos for facebook and instagram
• Mini logos for the phone and email?

```html
<!DOCTYPE html>
<html lang="en">
<head>
<meta charset="utf-8">
<title>The Harbourview Motion Clinic — Business Card</title>
<link href="https://fonts.googleapis.com/css2?family=Montserrat:wght@400;500;700;800&display=swap" rel="stylesheet">
<style>
  :root {
    --brand-blue: #0f58a8;
    --ink: #1d1d1f;
    --muted: #55585e;
    --rule: #6b6e73;
    --paper: #ffffff;
    --backdrop: #3a414c;
  }
  * { margin: 0; padding: 0; box-sizing: border-box; }
  html, body {
    width: 1200px; height: 1200px; overflow: hidden;
    background: var(--backdrop);
    font-family: "Montserrat", sans-serif;
  }
  .stage { position: relative; width: 1200px; height: 1200px; }

  .card {
    position: absolute; left: 220px;
    width: 760px; height: 459px;
    border-radius: 34px; overflow: hidden;
    box-shadow: 0 14px 30px rgba(0,0,0,.35);
  }

  /* Front */
  .card-front { top: 80px; background: var(--brand-blue); color: var(--paper); }
  .front-emblem {
    position: absolute; left: 110px; top: 88px;
    width: 282px; height: 282px; border-radius: 50%;
    background: var(--paper);
  }
  .front-wordmark { position: absolute; left: 430px; top: 176px; }
  .wordmark-title {
    font-weight: 800; font-size: 27px; letter-spacing: .5px; line-height: 1;
  }
  .wordmark-sub {
    font-weight: 800; font-size: 19px; letter-spacing: 8.6px; margin-top: 10px; line-height: 1;
  }

  /* Back */
  .card-back { top: 621px; background: var(--paper); color: var(--ink); }
  .side-strip {
    position: absolute; left: 0; top: 0; width: 170px; height: 100%;
    border-right: 1.5px solid var(--rule);
  }
  .side-wordmark {
    position: absolute; left: 85px; top: 230px;
    transform: translate(-50%, -50%) rotate(-90deg);
    white-space: nowrap; color: var(--brand-blue);
  }
  .side-wordmark .wordmark-title { font-size: 27px; }
  .side-wordmark .wordmark-sub { font-size: 19px; letter-spacing: 8.6px; }

  .rule { position: absolute; height: 0; border-top: 1.5px solid var(--rule); }
  .rule-top { left: 430px; right: 40px; top: 62px; }
  .rule-name { left: 170px; right: 40px; top: 215px; }
  .rule-contact { left: 170px; right: 40px; top: 372px; }
  .rule-appointment { left: 250px; right: 40px; top: 420px; border-top: 1.5px dashed #8a8d92; }

  .person { position: absolute; left: 215px; top: 118px; }
  .person-name { font-size: 34px; font-weight: 400; letter-spacing: .5px; }
  .person-name .accent { color: var(--brand-blue); }
  .person-role { font-size: 17px; color: var(--muted); margin-top: 4px; }

  .contact-list { position: absolute; left: 215px; top: 240px; list-style: none; }
  .contact-item {
    display: flex; align-items: center; gap: 16px;
    font-size: 21px; height: 40px; letter-spacing: .3px;
  }
  .contact-icon { width: 24px; height: 24px; flex: none; }
  .social-dot {
    width: 24px; height: 24px; border-radius: 50%; flex: none;
    background: var(--brand-blue);
  }
  .contact-social-right { position: absolute; left: 540px; top: 240px; }
  .contact-social-right .contact-item { font-size: 18px; }
</style>
</head>
<body>
<main class="stage">

  <section class="card card-front" aria-label="Card front">
    <div class="front-emblem"></div>
    <div class="front-wordmark">
      <div class="wordmark-title">THE HARBOURVIEW</div>
      <div class="wordmark-sub">MOTION CLINIC</div>
    </div>
  </section>

  <section class="card card-back" aria-label="Card back">
    <div class="side-strip">
      <div class="side-wordmark">
        <div class="wordmark-title">THE HARBOURVIEW</div>
        <div class="wordmark-sub">MOTION CLINIC</div>
      </div>
    </div>

    <div class="rule rule-top"></div>

    <div class="person">
      <div class="person-name">Name of <span class="accent">Person</span></div>
      <div class="person-role">Designation</div>
    </div>

    <div class="rule rule-name"></div>

    <ul class="contact-list">
      <li class="contact-item">
        <svg class="contact-icon" viewBox="0 0 24 24" aria-hidden="true">
          <circle cx="12" cy="12" r="10.5" fill="none" stroke="#1d1d1f" stroke-width="2"/>
          <path d="M9 7.5c-.6 0-1.3.6-1.3 1.5 0 3.5 3.8 7.3 7.3 7.3.9 0 1.5-.7 1.5-1.3l-1.8-1.4-1.3.8c-1.3-.6-2.6-1.9-3.2-3.2l.8-1.3z" fill="#1d1d1f"/>
        </svg>
        <span>555.018.2046</span>
      </li>
      <li class="contact-item">
        <svg class="contact-icon" viewBox="0 0 24 24" aria-hidden="true">
          <rect x="2" y="5" width="20" height="14" fill="#1d1d1f"/>
          <path d="M2 5l10 8 10-8" fill="none" stroke="#fff" stroke-width="1.6"/>
        </svg>
        <span>hello@harbourview.com</span>
      </li>
      <li class="contact-item">
        <span class="social-dot"></span>
        <span>community/name</span>
      </li>
    </ul>

    <ul class="contact-list contact-social-right">
      <li class="contact-item">
        <span class="social-dot"></span>
        <span>gallery_name</span>
      </li>
    </ul>

    <div class="rule rule-contact"></div>
    <div class="rule rule-appointment"></div>
  </section>

</main>
</body>
</html>
```